"Kestrava Inc." Needs a Logo Design and Business Card

The name of the company is "Kestrava Inc."
Our Business decription, which should appear on the front of the Business Card along with the logo and business name is:
"Boutique Global Procurement and Management Services"
We offer the following SERVICES that should be listed on the back of the Business Card :
"Consultants"
"Management"
"Business Research & Development"
"Sourcing Agent"
"Distributors"
We would like to see designs that use the colors
burnt orange and,
stainless steel
Business card designs should be innovatively modern and contemporary
Telephone number and email address should be on the back of the card
The name of the firm is "Kestrava Inc.
Industry/Entity Type
Steel
Look and feel
Each slider illustrates characteristics of the customer's brand and the style your logo design should communicate.

```html
<!DOCTYPE html>
<html lang="en">
<head>
<meta charset="utf-8">
<title>Kestrava Inc. — Business Card</title>
<link href="https://fonts.googleapis.com/css2?family=Dosis:wght@400&family=Didact+Gothic&display=swap" rel="stylesheet">
<style>
  :root {
    --burnt-orange: #f39200;
    --steel-grey: #6d6e71;
    --card-white: #ffffff;
    --backdrop: #d9d9db;
  }
  * { box-sizing: border-box; margin: 0; padding: 0; }
  html, body {
    width: 1200px;
    height: 1012px;
    overflow: hidden;
    background: var(--backdrop);
  }
  .sheet {
    position: relative;
    width: 1200px;
    height: 1012px;
    display: flex;
    flex-direction: column;
    align-items: center;
    justify-content: center;
    gap: 56px;
  }
  .card {
    position: relative;
    width: 760px;
    height: 434px;
    background: var(--card-white);
    box-shadow: 0 2px 6px rgba(0,0,0,0.12);
    font-family: "Dosis", sans-serif;
    color: var(--burnt-orange);
  }
  .card-frame {
    position: absolute;
    border: 2px solid var(--burnt-orange);
  }

  /* Front */
  .card--front .card-frame { inset: 26px; }
  .front-brand {
    position: absolute;
    left: 50%;
    top: 118px;
    transform: translateX(-50%);
    width: 330px;
  }
  .front-brand .brand-name {
    display: block;
    text-align: center;
    font-size: 58px;
    line-height: 1;
    letter-spacing: 1px;
    padding-bottom: 8px;
    white-space: nowrap;
  }
  .front-brand .brand-rule {
    display: block;
    height: 3px;
    background: var(--burnt-orange);
  }
  .front-brand .tagline {
    margin-top: 8px;
    text-align: right;
    font-size: 21px;
    line-height: 1.15;
    white-space: nowrap;
  }

  /* Back */
  .card--back .card-frame {
    left: 26px;
    right: 26px;
    top: 104px;
    bottom: 26px;
  }
  .back-brand {
    position: absolute;
    left: 30px;
    top: 22px;
    display: flex;
    align-items: center;
    gap: 14px;
  }
  .back-brand .brand-name {
    font-size: 40px;
    line-height: 1;
    letter-spacing: 1px;
    white-space: nowrap;
  }
  .back-brand .brand-divider {
    width: 2px;
    height: 48px;
    background: var(--burnt-orange);
  }
  .back-brand .tagline {
    font-size: 16px;
    line-height: 1.15;
    white-space: nowrap;
  }
  .services {
    position: absolute;
    left: 40px;
    right: 40px;
    top: 136px;
    font-family: "Didact Gothic", sans-serif;
    color: var(--steel-grey);
    font-size: 23px;
    line-height: 1.25;
    text-align: center;
    white-space: nowrap;
  }
  .services .dot {
    display: inline-block;
    width: 9px;
    height: 9px;
    border-radius: 50%;
    background: var(--steel-grey);
    vertical-align: middle;
    margin: 0 8px;
  }
  .contact {
    position: absolute;
    left: 44px;
    bottom: 80px;
    font-size: 19px;
    line-height: 1.3;
    white-space: nowrap;
  }
</style>
</head>
<body>
<main class="sheet">

  <section class="card card--front" aria-label="Business card front">
    <div class="card-frame"></div>
    <div class="front-brand">
      <span class="brand-name">Kestrava Inc.</span>
      <span class="brand-rule"></span>
      <p class="tagline">Worldwide Sourcing &amp; Supply<br>and Management Services</p>
    </div>
  </section>

  <section class="card card--back" aria-label="Business card back">
    <div class="card-frame"></div>
    <div class="back-brand">
      <span class="brand-name">Kestrava Inc.</span>
      <span class="brand-divider"></span>
      <p class="tagline">Worldwide Sourcing &amp; Supply<br>and Management Services</p>
    </div>
    <p class="services">
      Consultant<span class="dot"></span>Management<span class="dot"></span>Business Research &amp; Development<br>
      Sourcing Agent<span class="dot"></span>Distributor
    </p>
    <p class="contact">
      Cel. xx-xxx-xxx<br>
      Email. example@kestrava.com
    </p>
  </section>

</main>
</body>
</html>
```